Hi,
We are also sourcing for a logo, if you have ideas please take a look at our other project (if you look at our profile you should be able to see it).
We are looking for a website that will be used to manage mobile devices. The feature set is rather small, users can Wipe, Lock, Locate devices as well as make them Ring or Speak (by sending text to be spoken). We attached some images of what it looks like right now. We are looking for simplicity, uniformity and most importantly, the website should be thought of as primary User Interface, it should flow.
Please see attached to get an idea of what it looks like now. The current design was inspired by making a site that will work and flow well on a variety of displays (from mobile to tablet to desktop).
We want to stay away from radio buttons, check-boxes. This should be engaging and creative, opposite of Corporate. Not busy (ideally we are looking to have fewest possible choices at any given time and at the same time no feature should be more than 3 clicks away (this is a suggestion/approximation... just want to share our understanding of what 'flow' is).
Could be cartoony.
Thanks!
BrisketLoom
Reason: there are a couple of designs that are interesting, in addition to specific feedback I provided, possibly looking for more concepts.
Thank You

```html
<!DOCTYPE html>
<html lang="en">
<head>
<meta charset="utf-8">
<title>Device Manager</title>
<link rel="stylesheet" href="https://fonts.googleapis.com/css2?family=Mako&display=swap">
<style>
:root{
  --header:#2a4739;
  --header-line:#dfe6e2;
  --page:#ffffff;
  --ink:#3a3a3a;
  --ink-soft:#555;
  --panel-top:#ffffff;
  --panel-bottom:#e9e9e9;
  --panel-border:#d4d4d4;
  --tab-top:#ffffff;
  --tab-bottom:#e6e6e6;
  --tab-active-top:#4d6f5e;
  --tab-active-bottom:#213a2e;
  --cancel-top:#f9a05a;
  --cancel-bottom:#ec6f25;
  --wipe-top:#a5cf47;
  --wipe-bottom:#6a9c1c;
  --more-top:#5d8471;
  --more-bottom:#264537;
  --map-base:#eae6d8;
  --map-green:#cfe0b5;
}
*{box-sizing:border-box;margin:0;padding:0}
html,body{width:1011px;height:1200px;overflow:hidden;background:var(--page)}
body{position:relative;font-family:"Mako",sans-serif;color:var(--ink)}

.site-header{position:absolute;left:0;top:0;width:1011px;height:51px;background:var(--header);border-bottom:2px solid var(--header-line)}
.brand{position:absolute;left:74px;top:12px;display:flex;align-items:center;gap:10px;color:#fff;font-size:20px}
.brand-mark{width:24px;height:24px;background:#4f8a2e;border-radius:3px}
.main-nav{position:absolute;right:75px;top:14px;display:flex;gap:34px;font-size:16px;color:#fff}
.main-nav .has-menu::after{content:"";display:inline-block;margin-left:6px;vertical-align:middle;border:4px solid transparent;border-top:5px solid #fff;border-bottom:0}

.action-tabs{position:absolute;top:70px;left:0;width:1011px;height:46px}
.tab{position:absolute;top:0;width:57px;height:46px;display:flex;align-items:center;justify-content:center;font-size:16px;color:#222;background:linear-gradient(var(--tab-top),var(--tab-bottom));border:1px solid #d0d0d0;box-shadow:0 1px 2px rgba(0,0,0,.15)}
.tab.is-active{color:#fff;background:linear-gradient(var(--tab-active-top),var(--tab-active-bottom));border-color:#1c3026}
.tab.is-small{font-size:10px}

.confirm-panel{position:absolute;left:74px;top:137px;width:865px;height:122px;border:1px solid var(--panel-border);border-radius:8px;background:linear-gradient(var(--panel-top),var(--panel-bottom));box-shadow:0 1px 3px rgba(0,0,0,.12);text-align:center}
.confirm-title{margin-top:14px;font-size:25px;font-weight:400;color:#333}
.confirm-actions{display:flex;justify-content:center;gap:17px;margin-top:12px;padding-left:2px}
.btn-big{width:110px;height:39px;border-radius:6px;color:#fff;font-size:25px;line-height:39px;box-shadow:0 0 0 2px #fff,0 0 0 3px #ccc}
.btn-cancel{background:linear-gradient(var(--cancel-top),var(--cancel-bottom))}
.btn-wipe{background:linear-gradient(var(--wipe-top),var(--wipe-bottom))}

.device-map{position:absolute;left:139px;top:275px;width:736px;height:455px;background:linear-gradient(135deg,var(--map-green),var(--map-base) 45%,#efe2c2)}
.map-toggle{position:absolute;right:5px;top:5px;display:flex;font-family:Arial,sans-serif;font-size:10px;background:#fff;border:1px solid #999}
.map-toggle span{padding:3px 6px}
.map-toggle .on{font-weight:bold;border-right:1px solid #bbb}
.map-pin{position:absolute;left:365px;top:200px}

.info-card{position:absolute;top:781px;height:329px;border:1px solid #dcdcdc;box-shadow:0 1px 3px rgba(0,0,0,.12);background:#fff}
.info-card h2{position:absolute;left:21px;top:20px;font-size:21px;font-weight:400;color:#444}
.card-photo{position:absolute;left:21px;top:60px;width:184px;height:118px}
.card-text{position:absolute;left:21px;right:21px;top:191px;font-size:12px;line-height:15px;text-align:justify;color:var(--ink-soft)}
.btn-more{position:absolute;right:20px;top:289px;width:68px;height:26px;border-radius:5px;background:linear-gradient(var(--more-top),var(--more-bottom));color:#fff;font-size:12px;line-height:26px;text-align:center;box-shadow:0 0 0 2px #fff,0 0 0 3px #c9c9c9}

.site-footer{position:absolute;left:75px;right:71px;top:1149px;display:flex;justify-content:space-between;font-size:12px;color:#444}
.footer-links{display:flex;gap:6px}
</style>
</head>
<body>
<header class="site-header">
  <div class="brand"><span class="brand-mark"></span><span>Logo Comes Here</span></div>
  <nav class="main-nav">
    <span class="has-menu">admin</span><span>devices</span><span>settings</span><span>sign out</span>
  </nav>
</header>

<div class="action-tabs">
  <div class="tab is-active" style="left:291px">Wipe</div>
  <div class="tab" style="left:367px">lock</div>
  <div class="tab" style="left:443px">find</div>
  <div class="tab" style="left:519px">ring</div>
  <div class="tab" style="left:595px">speak</div>
  <div class="tab is-small" style="left:672px">Loading</div>
</div>

<section class="confirm-panel">
  <h1 class="confirm-title">This will erase all files on your device</h1>
  <div class="confirm-actions">
    <div class="btn-big btn-cancel">Cancel</div>
    <div class="btn-big btn-wipe">Wipe</div>
  </div>
</section>

<div class="device-map" role="img" aria-label="Street map showing the current device location">
  <div class="map-toggle"><span class="on">map</span><span>satellite</span></div>
  <svg class="map-pin" width="20" height="30" viewBox="0 0 20 30"><path d="M10 1a8 8 0 0 1 8 8c0 6-8 19-8 19S2 15 2 9a8 8 0 0 1 8-8z" fill="#e23b2e" stroke="#8a1b12"/><circle cx="10" cy="9" r="3" fill="#7a140c"/></svg>
</div>

<article class="info-card" style="left:74px;width:256px">
  <h2>Welcome</h2>
  <div class="card-photo" role="img" aria-label="Three smartphones side by side" style="background:linear-gradient(90deg,#2b2b2b,#6c6c6c,#2b2b2b);width:150px"></div>
  <p class="card-text">Lorem Ipsum is simply dummy text of the printing and typesetting industry. Lorem Ipsum has been the industry's standard dummy text ever since the 1500s, when an unknown printer took a galley of type and scrambled it to make a type specimen book.</p>
  <div class="btn-more">Read More</div>
</article>

<article class="info-card" style="left:367px;width:260px">
  <h2>Lost or Stolen Phone?</h2>
  <div class="card-photo" role="img" aria-label="Phone being taken from a jeans pocket" style="background:linear-gradient(90deg,#3f5c80,#8a9bb0 55%,#e9e9e9)"></div>
  <p class="card-text">Lorem Ipsum is simply dummy text of the printing and typesetting industry. Lorem Ipsum has been the industry's standard dummy text ever since the 1500s, when an unknown printer took a galley of type and scrambled it to make a type specimen book.</p>
  <div class="btn-more">Read More</div>
</article>

<article class="info-card" style="left:664px;width:276px">
  <h2>Protect &amp; Secure</h2>
  <div class="card-photo" role="img" aria-label="Toy bear holding a phone beside a laptop" style="background:radial-gradient(circle at 60% 45%,#d8d8d8,#f4f4f4 70%);width:140px"></div>
  <p class="card-text">Lorem Ipsum is simply dummy text of the printing and typesetting industry. Lorem Ipsum has been the industry's standard dummy text ever since the 1500s, when an unknown printer took a galley of type and scrambled it to make a type specimen book.</p>
  <div class="btn-more">Read More</div>
</article>

<footer class="site-footer">
  <span>Copyrights © 2012. All Rights Reserved.</span>
  <nav class="footer-links"><span>Terms and Conditions</span>|<span>Frequently Asked Questions</span>|<span>About</span>|<span>Contact</span></nav>
</footer>
</body>
</html>
```